High-end construction company needs a business card design

We need a modern looking business card that draws people in, is memorable and looks so good people will want to sick it on their fridges.
On the first side what is needed are:
Logo
My name - Tomasz Brelwik
Title - Managing Director
Website - www.varkelt.co.uk
Email - tomasz@varkelt.co.uk
Telephone - 020 5194 6281
Mobile - 07845139072
On the back side was is needed is a list of all the services we provide:
-Kitchen Renovations
-Bathroom Renovations
-House Renovations
-Garage Conversions
-Extensions
-Loft Conversions
-Conservatories
-Carpentry
-Tiling
-Electrical
-Plumbing & Heating
-Bricklaying
-Landscaping
-Decorating
-Plastering
We would like the colours to be the same shades as on the logo with grey or black for the words.
Target Market(s)
Anyone who needs building work done
Contact Information for Business Card
This business card is for a construction company which strives to deliver excellent service and quality.
The look and feel of the card should represent this.
Requirements
Must have
- On the first side what is needed are:
Logo
My name - Tomasz Brelwik
Title - Managing Director
Website - www.varkelt.co.uk
Email - tomasz@varkelt.co.uk
Telephone - 020 5194 6281
Mobile - 07845139072
Nice to have
- Cool looking features

```html
<!DOCTYPE html>
<html lang="en">
<head>
<meta charset="utf-8">
<title>Varkelt Construction Ltd – Business Card</title>
<link rel="stylesheet" href="https://fonts.googleapis.com/css2?family=Montserrat:wght@400;500;700&display=swap">
<style>
  :root {
    --bg: #3b3431;
    --card: #1c1c1c;
    --green: #5fcf3a;
    --text: #f2f2f2;
    --muted: #2f2f2f;
  }
  * { box-sizing: border-box; margin: 0; padding: 0; }
  html, body { width: 1200px; height: 716px; overflow: hidden; }
  body {
    background: var(--bg);
    font-family: "Montserrat", sans-serif;
    color: var(--text);
    display: flex;
    align-items: center;
    justify-content: center;
    gap: 30px;
  }
  .card {
    width: 560px;
    height: 320px;
    background: var(--card);
    border-bottom: 5px solid var(--green);
    border-right: 3px solid var(--green);
    position: relative;
    overflow: hidden;
    box-shadow: 0 14px 30px rgba(0,0,0,.45);
  }

  /* Back side: services */
  .services {
    list-style: none;
    position: absolute;
    left: 36px;
    top: 26px;
    font-size: 13.5px;
    line-height: 17.5px;
  }
  .services li { display: flex; align-items: center; gap: 10px; }
  .services li::before {
    content: "";
    width: 7px; height: 7px;
    border-radius: 50%;
    background: var(--green);
    flex: none;
  }
  .back-mark {
    position: absolute;
    right: 34px;
    bottom: 46px;
    text-align: right;
    color: var(--muted);
    font-weight: 700;
    line-height: 1;
  }
  .back-mark .word { display: block; font-size: 62px; letter-spacing: 1px; }
  .back-mark .sub { display: block; font-size: 17px; letter-spacing: 4px; margin-top: 6px; }

  /* Front side: identity */
  .brand {
    position: absolute;
    left: 34px;
    top: 112px;
    color: var(--green);
    font-weight: 700;
    line-height: 1;
    display: flex;
    align-items: flex-start;
    gap: 10px;
  }
  .brand .dot { width: 14px; height: 14px; background: var(--green); margin-top: 8px; }
  .brand .word { display: block; font-size: 54px; letter-spacing: 1px; }
  .brand .sub { display: block; font-size: 14px; letter-spacing: 3.6px; margin-top: 8px; }
  .divider {
    position: absolute;
    left: 318px;
    top: 54px;
    width: 2px;
    height: 212px;
    background: var(--green);
  }
  .contact {
    position: absolute;
    left: 340px;
    top: 62px;
    font-size: 13.5px;
    line-height: 20px;
  }
  .contact .name { color: var(--green); font-weight: 700; font-size: 19px; line-height: 24px; }
  .contact .title { margin-bottom: 12px; }
  .contact .address { margin-bottom: 10px; }
  .contact .row { display: flex; align-items: center; gap: 7px; }
  .contact svg { width: 11px; height: 11px; flex: none; }
</style>
</head>
<body>
  <section class="card card-back" aria-label="Back of card: services">
    <ul class="services">
      <li>Kitchen Renovations</li>
      <li>Bathroom Renovations</li>
      <li>House Renovations</li>
      <li>Garage Conversions</li>
      <li>Extensions</li>
      <li>Loft Conversions</li>
      <li>Conservatories</li>
      <li>Carpentry</li>
      <li>Tiling</li>
      <li>Electrical</li>
      <li>Plumbing &amp; Heating</li>
      <li>Bricklaying</li>
      <li>Landscaping</li>
      <li>Decorating</li>
      <li>Plastering</li>
    </ul>
    <div class="back-mark">
      <span class="word">VARKELT</span>
      <span class="sub">CONSTRUCTION LTD</span>
    </div>
  </section>

  <section class="card card-front" aria-label="Front of card: contact details">
    <div class="brand">
      <div>
        <span class="word">VARKELT</span>
        <span class="sub">CONSTRUCTION LTD</span>
      </div>
    </div>
    <div class="divider"></div>
    <div class="contact">
      <p class="name">Tomasz Brelwik</p>
      <p class="title">Managing Director</p>
      <p class="address">14 Harlow Mews,<br>London, E2 8QT</p>
      <p class="row">
        <svg viewBox="0 0 12 12" aria-hidden="true"><path d="M2.5 1l2 2.3-1 1.2a7 7 0 0 0 4 4l1.2-1 2.3 2-1.2 1.5C5.5 11 1 6.5 1 2.2z" fill="var(--green)"/></svg>
        020 5194 6281
      </p>
      <p class="row">
        <svg viewBox="0 0 12 12" aria-hidden="true"><rect x="3" y="0.8" width="6" height="10.4" rx="1" fill="none" stroke="var(--green)" stroke-width="1.3"/><circle cx="6" cy="9.2" r=".7" fill="var(--green)"/></svg>
        07845139072
      </p>
      <p class="row">
        <svg viewBox="0 0 12 12" aria-hidden="true"><rect x="0.8" y="2.5" width="10.4" height="7" fill="none" stroke="var(--green)" stroke-width="1.2"/><path d="M1 3l5 3.6L11 3" fill="none" stroke="var(--green)" stroke-width="1.2"/></svg>
        tomasz@varkelt.co.uk
      </p>
      <p class="row">
        <svg viewBox="0 0 12 12" aria-hidden="true"><circle cx="6" cy="6" r="5" fill="none" stroke="var(--green)" stroke-width="1.2"/><path d="M1 6h10M6 1c-2.5 3-2.5 7 0 10M6 1c2.5 3 2.5 7 0 10" fill="none" stroke="var(--green)" stroke-width="1"/></svg>
        www.varkelt.co.uk
      </p>
    </div>
  </section>
</body>
</html>
```